Buch-/E-Book-Cover für Referenzbuch der Industrie
Zielgruppe
Als Manufaktur einzigartiger Fachmedien präsentiert verlag-technova Schlüsseltechnologien und ihre Märkte. Faszination für Technik ist die Grundlage unserer Arbeit. Mehr als 30 Jahre verlegerische Erfahrung und das Verständnis für Technologiemärkte machen uns zu einem anerkannten Partner der Industrie.
Unsere Medienmarken knüpfen ein starkes und weit verzweigtes Netzwerk – Print und digital – , in dem sich Anbieter und Anwender von Technologien und Produkten in ihren Zielsetzungen wiederfinden.
Unsere Magazine, Events und Netzwerkveranstaltungen sowie kundenspezifische Kommunikations- & Strategiekampagnen setzen in ihren Zielmärkten Maßstäbe und genießen bei Lesern, Kunden und Partnern Vertrauen und Respekt.
Für das ausgeschriebene Projekt handelt es sich um unsere Referenzpublikation MACHINA.ahead LUMEVETA.
LUMEVETA {polynesisch: Freiraum}
Das Referenzbuch der Industrie. Für Vorwärtsdenker und Zukunftsmacher.
Wandel bestimmt unsere Zeit und verändert unsere Gesellschaft, unsere Unternehmen, uns alle.
Im Wandel liegt Freiraum zur Gestaltung. Gesellschaftlicher Wandel, Technologie-Wandel, Klimawandel, Wertewandel, Führungswandel oder Organisationswandel sind nur einige Beispiele. Wer dabei den Wandel in engen Bahnen denkt, verschenkt Potential. Veränderung braucht Freiraum für neue Ideen und Perspektiven sowie Persönlichkeiten, die diesen nutzen wollen.
Aber wer gestaltet die Zukunft der Industrie und ihrer Branchen? Und wie?
Wir geben Personen aus der Industrie den Freiraum, ihre Perspektiven auf und aus dem Wandel zu erzählen. Warum? Weil sie uns begeistert haben, in persönlichen Treffen und Gesprächen, durch streitbare Meinungen und ehrliche Geschichten. Weil sie die Zukunft verändern.
LUMEVETA ist eine Aufforderung: Zum Mitdenken, Weiterdenken, aber auch Nachdenken.
LUMEVETA – RAUM FÜR NEUES
Ein Referenzbuch, d..
Aufgabenstellung
1. Kurzzusammenfassung der Ausschreibung
Die 4. Ausgabe des jährlichen Referenzbuchs der Industrie, MACHINA.ahead LUMEVETA 2025, erscheint im Oktober 2024. Für das Cover sucht der verlag-technova Verlag neue Vorschläge, die die Themen Freiraum und Wandel in den Fokus stellen.
2. Gestalterische & Inhaltliche Anforderungen
• Format: 195x250 mm + Anschnitt
• Rücken: ca. 1,6 cm (Stand letzte Publikation 2023)
• Auflösung: Druckqualität, mind. 300 dpi
• Inhaltliche Elemente:
- LUMEVETA Schriftzug
- {polynesisch: Freiraum}
- Untersatz: Das Referenzbuch der Industrie. Für Vorwärtsdenker und Zukunftsmacher.
- part of MACHINA.ahead Logo-Balken am unteren Rand (siehe Beispiel AuD_Titelbeispiel_Logobalken)
WICHTIG: Der aktuelle Schriftzug LUMEVETA und die Farbe Orange (0/80/100/0) (siehe Beispiel LUMEVETA 2021) sollen als Wiedererkennung in die Gestaltungen eingebunden werden.

```html
<!DOCTYPE html>
<html lang="de">
<head>
<meta charset="utf-8">
<title>MACHINA.ahead LUMEVETA 2025 – Cover</title>
<link rel="stylesheet" href="https://fonts.googleapis.com/css2?family=Oswald:wght@500;700&family=Barlow+Semi+Condensed:wght@500;600&display=swap">
<style>
  :root {
    --orange: #e8521b;
    --ink: #0d0d0d;
    --paper: #ffffff;
    --stage: #ffffff;
  }
  * { margin: 0; padding: 0; box-sizing: border-box; }
  html, body {
    width: 1200px; height: 720px; overflow: hidden;
    background: var(--stage);
  }
  .canvas { position: relative; width: 1200px; height: 720px; }

  /* Spine */
  .spine {
    position: absolute; left: 301px; top: 52px;
    width: 48px; height: 616px;
    background: var(--orange);
    box-shadow: 0 1px 3px rgba(0,0,0,.18);
    overflow: hidden;
  }
  .spine-emblem {
    position: absolute; left: 7px; top: 32px;
    width: 34px; height: 34px; border-radius: 50%;
    background: var(--paper);
  }
  .spine-title {
    position: absolute; left: 0; right: 0; top: 146px;
    font-family: "Oswald", sans-serif; font-weight: 700;
    font-size: 32px; line-height: 36px; color: var(--ink);
    text-align: center;
  }
  .spine-title span {
    display: block; transform: scaleX(0.9);
  }
  .spine-year {
    position: absolute; left: 0; right: 0; top: 296px;
    font-family: "Oswald", sans-serif; font-weight: 700;
    font-size: 22px; line-height: 1; color: var(--paper); text-align: center;
  }
  .spine-claim {
    position: absolute; left: 18px; top: 333px;
    writing-mode: vertical-rl;
    transform: rotate(180deg);
    white-space: nowrap;
    font-family: "Barlow Semi Condensed", sans-serif; font-weight: 500;
    font-size: 8.5px; line-height: 12px; color: var(--paper);
  }

  /* Front cover */
  .cover {
    position: absolute; left: 419px; top: 52px;
    width: 480px; height: 616px;
    background: var(--orange);
    box-shadow: 0 1px 3px rgba(0,0,0,.18);
    overflow: hidden;
  }
  .cover-wordmark {
    position: absolute; left: 0; top: 0; width: 200px; height: 616px;
    font-family: "Oswald", sans-serif; font-weight: 700;
    font-size: 184px; line-height: 184px;
    color: var(--ink);
  }
  .cover-wordmark span {
    position: absolute; left: -3px;
    transform: scaleX(0.84); transform-origin: left top;
    white-space: nowrap;
  }
  .cover-wordmark .row-1 { top: -35px; }
  .cover-wordmark .row-2 { top: 119px; }
  .cover-wordmark .row-3 { top: 287px; }
  .cover-wordmark .row-4 { top: 441px; }
  .cover-translation {
    position: absolute; left: 26px; top: 302px;
    font-family: "Barlow Semi Condensed", sans-serif; font-weight: 600;
    font-size: 9px; line-height: 12px; color: var(--paper);
  }
  .cover-illustration {
    position: absolute; left: 232px; top: 48px;
    width: 186px; height: 246px;
    border-radius: 93px 93px 6px 6px;
    background: var(--paper);
  }
  .cover-year {
    position: absolute; left: 229px; width: 190px; top: 302px;
    font-family: "Oswald", sans-serif; font-weight: 500;
    font-size: 42px; line-height: 1; color: var(--ink);
    text-align: center;
  }
  .cover-claim {
    position: absolute; left: 215px; width: 220px; top: 356px;
    font-family: "Barlow Semi Condensed", sans-serif; font-weight: 600;
    font-size: 11.5px; line-height: 14.5px; color: var(--paper);
    text-align: center;
  }
  .cover-brandbar {
    position: absolute; left: 261px; top: 573px;
    display: flex; align-items: baseline; gap: 5px;
    color: var(--ink);
    font-family: "Oswald", sans-serif; font-weight: 500;
  }
  .brandbar-prefix { font-size: 8px; }
  .brandbar-name { font-size: 15px; letter-spacing: 0.2px; }
</style>
</head>
<body>
<div class="canvas">
  <div class="spine">
    <div class="spine-emblem" role="img" aria-label="Kleine Illustration: Kopf mit Zahnrädern"></div>
    <div class="spine-title"><span>LU</span><span>ME</span><span>VE</span><span>TA</span></div>
    <div class="spine-year">2025</div>
    <div class="spine-claim">Das Referenzbuch der Industrie. Für Vorwärtsdenker und Zukunftsmacher.</div>
  </div>

  <div class="cover">
    <h1 class="cover-wordmark">
      <span class="row-1">LU</span>
      <span class="row-2">ME</span>
      <span class="row-3">VE</span>
      <span class="row-4">TA</span>
    </h1>
    <p class="cover-translation">(polynesisch – Freiraum)</p>
    <div class="cover-illustration" role="img" aria-label="Illustration: Kopfbüste im Profil mit Zahnrädern im weißen Kreis"></div>
    <p class="cover-year">2025</p>
    <p class="cover-claim">Das Referenzbuch der Industrie.<br>Für Vorwärtsdenker<br>und Zukunftsmacher.</p>
    <div class="cover-brandbar">
      <span class="brandbar-prefix">part of</span>
      <span class="brandbar-name">MACHINA.ahead</span>
    </div>
  </div>
</div>
</body>
</html>
```